Preisliste für Kosmetikinstitut
Zielgruppe
Ich benötige für mein Kosmetikinstitut eine Preisliste für die moderne Frau, aber auch Männer. Das Design sollte mein Logo enthalten. Farben des Designkonzepts einbauen.
A4 quer zum Falten, wie ein Heft, 1. Seite Preisliste mit logo, im Innenteil dann Anwendungen
Aufgabenstellung
Minimalistisch, ästhetisch, modern, edel
Kontaktdaten auf der Rückseite
LB Hautatelier
Lotte Brenner
Lindenhang 17
83671 Waakirchen
EMail: lotte@lb-hautatelier.de
Whatsapp: 0176 284 9017

```html
<!DOCTYPE html>
<html lang="de">
<head>
<meta charset="utf-8">
<title>LB Hautatelier – Preisliste</title>
<link rel="stylesheet" href="https://fonts.googleapis.com/css2?family=Quicksand:wght@400;500;600;700&family=Kaushan+Script&display=swap">
<style>
:root{
  --backdrop:#a0a0a0;
  --paper:#eeeeee;
  --taupe:#8a857a;
  --taupe-dark:#6f6a60;
  --peach:#ebd3c1;
  --white:#ffffff;
}
*{box-sizing:border-box;margin:0;padding:0}
html,body{width:962px;height:1200px;overflow:hidden;background:var(--backdrop)}
body{position:relative;font-family:"Quicksand",sans-serif;color:var(--taupe)}
.sheet{position:absolute;left:120px;width:720px;height:508px;background:var(--paper);overflow:hidden}
.sheet--facial{top:77px}
.sheet--device{top:605px}
.leaf{position:absolute}
.leaf--corner{left:0;top:0;width:118px;height:62px;background:linear-gradient(135deg,var(--taupe) 0%,rgba(138,133,122,0) 90%);opacity:.75}
.leaf--frond{right:0;top:0;width:258px;height:140px;background:radial-gradient(ellipse at 60% 30%,var(--peach) 0%,rgba(235,211,193,.5) 55%,rgba(235,211,193,0) 80%)}
.brand{position:absolute;left:34px;top:80px;font-size:18px;font-weight:500;color:var(--taupe);white-space:nowrap;line-height:1}
.headline{position:absolute;left:276px;top:52px;font-family:"Kaushan Script",cursive;font-size:49px;color:var(--taupe);line-height:1}
.category{position:absolute;left:472px;top:75px;width:250px;height:27px;background:var(--taupe);border-radius:14px 0 0 14px;color:var(--white);font-weight:700;font-size:15px;line-height:27px;padding-left:36px;letter-spacing:.2px}
.sheet--device .category{padding-left:14px}
.item{position:absolute;width:300px}
.item--l{left:37px}
.item--r{left:370px;width:315px}
.item__title{position:relative;padding-left:12px;font-size:10.2px;font-weight:600;color:var(--taupe);line-height:14px;white-space:nowrap}
.item__title::before{content:"";position:absolute;left:0;top:5px;width:4px;height:4px;background:var(--taupe);transform:rotate(45deg)}
.item__text{padding-left:12px;font-size:6.5px;line-height:8.2px;color:var(--taupe);margin-top:2px;white-space:nowrap}
.item__text + .item__text{margin-top:5px}
.item__sub{padding-left:12px;font-size:6.4px;font-weight:700;margin-top:2px}
.price{position:absolute;height:15.5px;background:var(--peach);display:flex;justify-content:space-between;align-items:center;padding:0 11px;font-size:9px;font-weight:600;color:var(--taupe-dark);white-space:nowrap}
.price--l{left:49px;width:298px}
.price--r{left:385px;width:297px}
.steps{position:absolute;left:49px;top:0;width:290px}
.step{position:absolute;left:0;width:290px}
.step__num{position:absolute;left:3px;top:0;width:11px;height:11px;background:var(--taupe);transform:rotate(45deg)}
.step__num span{display:block;transform:rotate(-45deg);color:var(--white);font-size:6px;font-weight:700;text-align:center;line-height:11px}
.step__text{position:absolute;left:28px;top:-1px;width:265px;font-size:6.5px;line-height:8.2px;white-space:nowrap}
.web{position:absolute;left:528px;font-size:12.5px;font-weight:600;color:var(--taupe);display:flex;align-items:center;gap:9px;white-space:nowrap}
.web svg{width:10px;height:10px}
</style>
</head>
<body>

<section class="sheet sheet--facial">
  <div class="leaf leaf--corner" role="img" aria-label="Palmblatt-Illustration in Taupe"></div>
  <div class="leaf leaf--frond" role="img" aria-label="Große Palmwedel-Illustration in Pfirsich"></div>
  <div class="brand">LB Hautatelier</div>
  <div class="headline">Preisliste</div>
  <div class="category">Gesichtsbehandlungen</div>

  <div class="item item--l" style="top:149px">
    <div class="item__title">Express Facial Treatment</div>
    <p class="item__text">Für alle, die wenig Zeit haben und trotzdem ihre Haut auffrischen und revitalisieren wollen.<br>Reinigung, Enzympeeling, Serum, Maske, Abschlusspflege</p>
  </div>
  <div class="price price--l" style="top:188px"><span>35-45 Min.</span><span>€ 59,00</span></div>

  <div class="item item--l" style="top:227px">
    <div class="item__title">Classic Facial Treatment – Klassische Gesichtsbehandlung</div>
    <p class="item__text">Reinigung, Enzympeeling, Vapozon, Ausreinigung, Augenbrauenkorrektur, Ampulle,<br>Maske, individuelle Abschlusspflege</p>
  </div>
  <div class="price price--l" style="top:266px"><span>45-60 Min.</span><span>€ 89,00</span></div>

  <div class="item item--l" style="top:302px">
    <div class="item__title">Clear Skin Treatment</div>
    <p class="item__text">Die Haut wirkt ausgeglichener, Unreinheiten wird vorgebeugt, der Teint erhält Balance<br>und kann sich beruhigen. Gleichzeitig wird die Haut durch die Hyaluronsäure vitalisiert und<br>Falten und Fältchen kann entgegengewirkt werden.</p>
  </div>
  <div class="price price--l" style="top:349px"><span>50-60 Min.</span><span>€ 89,00</span></div>

  <div class="item item--l" style="top:389px">
    <div class="item__title">Capilarine Treatment</div>
    <p class="item__text">Hautrötungen und Couperose Erscheinungen werden gelindert, die Gefäßwände werden<br>gestärkt und das Hautbild wirkt ausgeglichener, mögliche Irritationen gehen zurück.<br>Gleichzeitig sorgt die hochkonzentrierte Hyaluronsäure für Frische, Vitalität und Glätte.</p>
  </div>
  <div class="price price--l" style="top:436px"><span>50-60 Minuten</span><span>€ 89,00</span></div>

  <div class="item item--r" style="top:149px">
    <div class="item__title">Calmessa Soft Treatment (für die empfindliche, gereizte Haut)</div>
    <p class="item__text">Entzündliche Prozesse können gemildert werden, gereizte Haut oder solche, die wenig<br>verträgt, wird beruhigt. Irritationen können zurückgehen, die Haut erhält Balance.</p>
  </div>
  <div class="price price--r" style="top:188px"><span>ca. 50 Minuten</span><span>€ 79,00</span></div>

  <div class="item item--r" style="top:227px">
    <div class="item__title">Vitamin Soft Boost</div>
    <p class="item__text">Vitamine sorgen für Power und Frische in und auf der Haut, die Widerstandskraft der Haut<br>wird gestärkt. Die Faltentiefe kann gemildert werden.</p>
  </div>
  <div class="price price--r" style="top:266px"><span>ca. 50 Minuten</span><span>€ 79,00</span></div>

  <div class="item item--r" style="top:302px">
    <div class="item__title">Anti-Age Advanced</div>
    <p class="item__text">Die Haut wirkt insgesamt erfrischt, vitalisiert und gestrafft.<br>Feine Linien und Fältchen werden reduziert.</p>
  </div>
  <div class="price price--r" style="top:349px"><span>50-70 Minuten (je nach Peeling)</span><span>€ 99,00</span></div>

  <div class="item item--r" style="top:389px">
    <div class="item__title">Chemisches Peeling (Oktober – April)</div>
    <p class="item__text">Professionelle Peelings können viele Problemstellungen lindern, verbessern oder gar<br>beheben. Dazu gehören die Zellerneuerung, Glättung der Hauttextur,<br>Reduzierung von Pigmentflecken, Verbesserung von Akne</p>
  </div>

  <div class="web" style="top:464px">
    <svg viewBox="0 0 10 10" aria-hidden="true"><circle cx="5" cy="5" r="4.3" fill="none" stroke="currentColor" stroke-width="1"/><ellipse cx="5" cy="5" rx="1.9" ry="4.3" fill="none" stroke="currentColor" stroke-width=".8"/><line x1=".7" y1="5" x2="9.3" y2="5" stroke="currentColor" stroke-width=".8"/></svg>
    www.lb-hautatelier.de
  </div>
</section>

<section class="sheet sheet--device">
  <div class="leaf leaf--corner" role="img" aria-label="Palmblatt-Illustration in Taupe"></div>
  <div class="leaf leaf--frond" role="img" aria-label="Große Palmwedel-Illustration in Pfirsich"></div>
  <div class="brand">LB Hautatelier</div>
  <div class="headline">Preisliste</div>
  <div class="category">Apparative Behandlungen</div>

  <div class="item item--l" style="top:139px">
    <div class="item__title">HydraPure – „Glowing Skin“ Treatment</div>
    <p class="item__sub">In 6 Schritten zu einer Haut mit einmaligem Glow- Effekt</p>
  </div>
  <div class="steps">
    <div class="step" style="top:178px"><div class="step__num"><span>1</span></div><p class="step__text">Behandlungsschritt: die Haut wird tiefengereinigt</p></div>
    <div class="step" style="top:196px"><div class="step__num"><span>2</span></div><p class="step__text">Behandlungsschritt: die obersten Verhornungen und Schuppen werden sanft<br>mit einem Peeling gelöst</p></div>
    <div class="step" style="top:218px"><div class="step__num"><span>3</span></div><p class="step__text">Behandlungsschritt: die Haut wird in der Tiefe gereinigt und entschlackt</p></div>
    <div class="step" style="top:236px"><div class="step__num"><span>4</span></div><p class="step__text">Behandlungsschritt: niedermolekulare Wirkstoffe werden aufgebracht, um die<br>Haut zu erfrischen und den entsprechenden Glow zu geben</p></div>
    <div class="step" style="top:260px"><div class="step__num"><span>5</span></div><p class="step__text">Ausgewählte und hochdosierte Wirkstoffessenzen werden auf die Haut<br>gesprüht und durch die niedrige Molekularstruktur können<br>diese tiefer in der Haut wirken</p></div>
    <div class="step" style="top:292px"><div class="step__num"><span>6</span></div><p class="step__text">Zum Schluss werden die Essenzen durch eine Impulsgebende Druckluftmassage<br>noch tiefer in die Haut gebracht</p></div>
  </div>
  <div class="price price--l" style="top:316px"><span>60 Minuten</span><span>€ 140,00</span></div>

  <div class="item item--l" style="top:348px">
    <div class="item__title">Mikrodermabrasion</div>
    <p class="item__text">Bei der Mikrodermabrasion handelt es sich um ein mechanisches Hautpeeling, dabei<br>werden mittels feinster Kristalle die Hornzellen der obersten Hautschicht schonend<br>abgetragen und dann mit Hilfe eines Unterdrucks behutsam abgesaugt.<br>Der revitalisierende Prozess erhöht die Durchblutung, fördert die Zellerneuerung und<br>verleiht ihrer Haut ein zartes frisches Gefühl. Die Haut gewinnt an Spannkraft, feine<br>Fältchen werden gemildert und Poren sichtbar verkleinert. Außerdem hilft es<br>bei oberflächlichen Akne Narben, Pigmentstörungen und Dehnungsstreifen. Wirkstoffe<br>können nun wieder besser von der Haut aufgenommen werden.</p>
  </div>
  <div class="price price--l" style="top:437px"><span>Gesicht</span><span>€ 89,00</span></div>
  <div class="price price--l" style="top:458px"><span>Gesicht, Hals, Dekolleté</span><span>€ 110,00</span></div>

  <div class="item item--r" style="top:139px">
    <div class="item__title">Microneedling</div>
    <p class="item__text">Die Behandlung eignet sich besonders für Menschen, die ihre Hautqualität verbessern<br>und Falten, (Akne)Narben, Pigmentverschiebungen, große Poren und sogar Haarausfall<br>behandeln wollen.</p>
    <p class="item__text">Mit Hilfe feinster Nadeln werden der Haut kontrolliert Mikroverletzungen zugeführt,<br>dies regt die natürliche Wundheilung, sowie Kollagen- und Elastin Bildung an.<br>Microneedling ist also eine natürliche Beauty-Behandlung, die körpereigene<br>Reparaturmechanismen nutzt, um ein strafferes Hautbild zu erhalten. Bereits nach der<br>ersten Behandlung sieht die Haut aufgepolstert, frisch und rosig aus. Kleine Linien<br>und Fältchen werden tiefenbehandelt. Die Haut wirkt straffer und jugendlicher.<br>Ein weiterer Vorteil, durch die Stichkanäle können Wirkstoffe besser von der Haut<br>aufgenommen werden.</p>
  </div>
  <div class="price price--r" style="top:263px"><span>Gesicht</span><span>€ 110,00</span></div>
  <div class="price price--r" style="top:284px"><span>Gesicht, Hals</span><span>€ 130,00</span></div>
  <div class="price price--r" style="top:305px"><span>Gesicht, Hals, Dekolleté</span><span>€ 150,00</span></div>

  <div class="item item--r" style="top:344px">
    <div class="item__title">Zusatzleistungen</div>
  </div>
  <div class="price price--r" style="top:363px"><span>Augenbrauen zupfen</span><span>€ 8</span></div>
  <div class="price price--r" style="top:384px"><span>Augenbrauen färben</span><span>€ 12</span></div>
  <div class="price price--r" style="top:405px"><span>Wimpern färben</span><span>€ 15</span></div>
  <div class="price price--r" style="top:426px"><span>Enthaarung störender Gesichtsbehaarung mittels Wax</span><span>€ 10-30</span></div>

  <div class="web" style="top:461px">
    <svg viewBox="0 0 10 10" aria-hidden="true"><circle cx="5" cy="5" r="4.3" fill="none" stroke="currentColor" stroke-width="1"/><ellipse cx="5" cy="5" rx="1.9" ry="4.3" fill="none" stroke="currentColor" stroke-width=".8"/><line x1=".7" y1="5" x2="9.3" y2="5" stroke="currentColor" stroke-width=".8"/></svg>
    www.lb-hautatelier.de
  </div>
</section>

</body>
</html>
```